BOLD & MINIMALIST DESIGN NEEDED

We want a very bold but minimalistic business card design that is impactful and utilizes both sides of the business card. Our current logo is included for your use.

We want bold fonts and good use of negative space. We don't want the logo to overpower the design.

Target Market(s)

Professionals who are building new commercial buildings.

Industry/Entity Type

Construction

Contact Information for Business Card

Name, Title, email, office phone, cell phone, website

Font styles to use
Serif
Sans Serif

Requirements
Must have
• Bold design!

```html
<!DOCTYPE html>
<html lang="en">
<head>
<meta charset="utf-8">
<title>Ridgeline Design + Build — Business Card</title>
<link rel="stylesheet" href="https://fonts.googleapis.com/css2?family=Montserrat:wght@400;500;700;800&display=swap">
<style>
  :root {
    --stage: #2b2c2e;
    --card-white: #ffffff;
    --card-dark: #1c1d1f;
    --brand-green: #7ac143;
    --ink: #111111;
    --paper-text: #f2f2f2;
  }
  * { margin: 0; padding: 0; box-sizing: border-box; }
  html, body { width: 1200px; height: 874px; overflow: hidden; }
  body {
    background: var(--stage);
    font-family: "Montserrat", sans-serif;
    display: flex;
    flex-direction: column;
    align-items: center;
    justify-content: center;
    gap: 30px;
  }
  .card {
    position: relative;
    width: 700px;
    height: 400px;
    border-radius: 22px;
    overflow: hidden;
    background: var(--card-white);
  }

  /* Front */
  .front { display: flex; align-items: center; justify-content: center; }
  .brand { display: flex; align-items: center; gap: 18px; color: var(--ink); font-weight: 800; }
  .brand-mark { width: 56px; height: 56px; background: var(--brand-green); }
  .brand-name { display: flex; flex-direction: column; line-height: 1; }
  .front .brand-name .word { font-size: 64px; letter-spacing: 1px; }
  .front .brand-name .tag { font-size: 22px; letter-spacing: 9px; margin-top: 8px; }

  /* Back */
  .back-shape { position: absolute; inset: 0; width: 100%; height: 100%; }
  .back .brand { position: absolute; right: 46px; top: 100px; gap: 12px; }
  .back .brand-mark { width: 30px; height: 30px; }
  .back .brand-name .word { font-size: 34px; }
  .back .brand-name .tag { font-size: 12px; letter-spacing: 5px; margin-top: 5px; }

  .person { position: absolute; left: 40px; top: 186px; color: var(--paper-text); }
  .person-name { color: var(--brand-green); font-weight: 700; font-size: 28px; letter-spacing: 1px; line-height: 1.1; }
  .person-title { font-size: 14px; font-weight: 500; letter-spacing: 1px; margin-top: 4px; }
  .contact-list { list-style: none; margin-top: 14px; }
  .contact-list li { display: flex; align-items: center; gap: 10px; font-size: 16px; line-height: 1.3; margin-bottom: 6px; }
  .contact-list svg { width: 14px; height: 14px; fill: var(--brand-green); flex: none; }

  .follow { position: absolute; right: 46px; bottom: 88px; display: flex; align-items: center; gap: 8px; color: var(--paper-text); font-size: 16px; font-weight: 500; }
  .follow-label { margin-right: 4px; }
  .social-dot { width: 20px; height: 20px; border-radius: 50%; background: var(--brand-green); }
  .address { position: absolute; right: 46px; bottom: 26px; color: var(--paper-text); font-size: 18px; line-height: 1.4; text-align: left; }
</style>
</head>
<body>

  <section class="card front" aria-label="Card front">
    <div class="brand">
      <span class="brand-mark"></span>
      <span class="brand-name"><span class="word">RIDGELINE</span><span class="tag">DESIGN + BUILD</span></span>
    </div>
  </section>

  <section class="card back" aria-label="Card back">
    <svg class="back-shape" viewBox="0 0 700 400" preserveAspectRatio="none" aria-hidden="true">
      <rect width="700" height="400" fill="var(--card-dark)"/>
      <path d="M0,0 H700 V264 C420,244 200,154 0,64 Z" fill="var(--brand-green)"/>
      <path d="M0,0 H700 V250 C420,230 200,140 0,60 Z" fill="var(--card-white)"/>
    </svg>

    <div class="brand">
      <span class="brand-mark"></span>
      <span class="brand-name"><span class="word">RIDGELINE</span><span class="tag">DESIGN + BUILD</span></span>
    </div>

    <div class="person">
      <h1 class="person-name">DANIEL MARSH</h1>
      <p class="person-title">OWNER-CEO</p>
      <ul class="contact-list">
        <li><svg viewBox="0 0 24 24"><path d="M6.6 10.8a15 15 0 0 0 6.6 6.6l2.2-2.2c.3-.3.7-.4 1-.2 1.1.4 2.3.6 3.6.6.6 0 1 .4 1 1V20c0 .6-.4 1-1 1A17 17 0 0 1 3 4c0-.6.4-1 1-1h3.5c.6 0 1 .4 1 1 0 1.3.2 2.5.6 3.6.1.3 0 .7-.2 1z"/></svg>123 456 789</li>
        <li><svg viewBox="0 0 24 24"><path d="M7 1h10a2 2 0 0 1 2 2v18a2 2 0 0 1-2 2H7a2 2 0 0 1-2-2V3a2 2 0 0 1 2-2zm0 3v15h10V4z"/></svg>123 456 789</li>
        <li><svg viewBox="0 0 24 24"><path d="M2 5h20v14H2zm2 2v.5l8 5 8-5V7z"/></svg>info@yourmail.com</li>
        <li><svg viewBox="0 0 24 24"><circle cx="12" cy="12" r="10"/></svg>www.yourwebsite.com</li>
      </ul>
    </div>

    <div class="follow"><span class="follow-label">Follow Us:</span>
      <span class="social-dot"></span><span class="social-dot"></span><span class="social-dot"></span>
    </div>
    <p class="address">Your address, City<br>State, Zip 1234</p>
  </section>

</body>
</html>
```